Ecard for facebook and Instagram postings

I need 4 ecards (don't know if that is what it is called) for Facebook and Instagram postings. My Logo and company name should be incorporated and also be square. I would like to be able to insert text as I need. Examples are:

https://www.plorvexa.com/photo.php?fbid=20262841672382489&set=a.20261729249182489.516031.71298967488&type=1&relevant_count=1

https://media-a-kpt.yy.plorvexacdn.net/hpics-bmk4/2345967_657092986477056_308792573_n.jpg

I don't necessarily need images on them, just the color scheme to my business cards and the logo and business name. But if you'd like to give it an interesting look, you can go ahead and play with it. My site is tornquillmentoring.com, if you'd like to see the style of it.

Thank you!!!
Updates

I just uploaded the logo in two variations.  Thank you!

Target Market(s)

Women 16-65

Industry/Entity Type

Business

Requirements
Must have
• Logo and business name
Should not have
• No white background. I have attached business card picture so you can have an idea of what I'd like.

```html
<!DOCTYPE html>
<html lang="en">
<head>
<meta charset="utf-8">
<title>Tornquill Mentoring Services – Quote Card</title>
<link rel="stylesheet" href="https://fonts.googleapis.com/css2?family=Tinos:wght@400;700&family=Montserrat:wght@500;600&display=swap">
<style>
  :root {
    --band-orange: #f39a2b;
    --band-orange-light: #f8b14d;
    --peach-centre: #fdebd2;
    --peach-mid: #fbd3a0;
    --peach-edge: #f6b266;
    --brand-red: #b8222b;
    --swoosh-red: #c4232e;
    --ink: #0d0d0d;
    --url-grey: #8a3a3d;
    --footer-light: #fff6ec;
  }
  html, body {
    margin: 0;
    padding: 0;
    width: 1200px;
    height: 1200px;
    overflow: hidden;
    background: var(--peach-mid);
  }
  .quote-card {
    position: relative;
    width: 1200px;
    height: 1200px;
    overflow: hidden;
  }
  .card-backdrop {
    position: absolute;
    inset: 0;
    background: radial-gradient(circle at 50% 45%, var(--peach-centre) 0%, var(--peach-mid) 55%, var(--peach-edge) 100%);
  }
  .top-band {
    position: absolute;
    left: 0; top: 0;
    width: 1200px; height: 23px;
    background: linear-gradient(90deg, var(--band-orange), var(--band-orange-light), var(--band-orange));
  }
  .quote-mark {
    position: absolute;
    font-family: "Tinos", "Times New Roman", serif;
    font-weight: 700;
    color: var(--brand-red);
    font-size: 330px;
    line-height: 1;
  }
  .quote-mark--open { left: 62px; top: 60px; }
  .quote-mark--close { left: 950px; top: 805px; }
  .quote-text {
    position: absolute;
    left: 150px;
    top: 222px;
    width: 900px;
    margin: 0;
    text-align: center;
    font-family: "Tinos", "Times New Roman", serif;
    font-weight: 700;
    font-size: 92px;
    line-height: 100px;
    color: var(--ink);
  }
  .footer-art {
    position: absolute;
    left: 0; top: 0;
    width: 1200px; height: 1200px;
  }
  .brand-name {
    position: absolute;
    left: 28px;
    top: 1012px;
    margin: 0;
    font-family: "Tinos", "Times New Roman", serif;
    font-weight: 400;
    font-size: 84px;
    line-height: 1;
    color: var(--brand-red);
  }
  .brand-tagline {
    position: absolute;
    left: 30px;
    top: 1132px;
    margin: 0;
    font-family: "Montserrat", Arial, sans-serif;
    font-weight: 600;
    font-size: 25px;
    letter-spacing: 6px;
    color: var(--brand-red);
  }
  .brand-url {
    position: absolute;
    left: 520px;
    top: 1133px;
    margin: 0;
    font-family: "Montserrat", Arial, sans-serif;
    font-weight: 500;
    font-size: 23px;
    letter-spacing: 1px;
    color: var(--url-grey);
  }
  .brand-badge {
    position: absolute;
    left: 1022px;
    top: 1032px;
    width: 112px;
    height: 112px;
    border-radius: 50%;
    background: var(--band-orange);
    border: 6px solid #ffffff;
    box-shadow: 0 0 0 3px var(--band-orange-light);
  }
</style>
</head>
<body>
  <main class="quote-card">
    <div class="card-backdrop" role="img" aria-label="Warm peach background with soft decorative paisley swirls"></div>
    <div class="top-band"></div>

    <span class="quote-mark quote-mark--open" aria-hidden="true">“</span>
    <p class="quote-text">Ignorance is the curse of God; knowledge is the wing wherewith we fly to heaven</p>
    <span class="quote-mark quote-mark--close" aria-hidden="true">”</span>

    <svg class="footer-art" viewBox="0 0 1200 1200" aria-hidden="true">
      <defs>
        <linearGradient id="footerFade" x1="0" y1="0" x2="0" y2="1">
          <stop offset="0" stop-color="#fff6ec" stop-opacity="0.6"/>
          <stop offset="1" stop-color="#fff6ec" stop-opacity="1"/>
        </linearGradient>
      </defs>
      <path class="footer-light" d="M0 955 C 350 905, 800 960, 1200 1130 L1200 1175 L0 1175 Z" fill="url(#footerFade)"/>
      <path class="swoosh" d="M0 955 C 350 905, 800 960, 1200 1130 L1200 1152 C 800 985, 350 925, 0 968 Z" fill="var(--swoosh-red)"/>
      <rect class="bottom-band" x="0" y="1175" width="1200" height="25" fill="var(--swoosh-red)"/>
    </svg>

    <p class="brand-name">Tornquill</p>
    <p class="brand-tagline">MENTORING SERVICES</p>
    <p class="brand-url">tornquillmentoring.com</p>
    <div class="brand-badge" aria-hidden="true"></div>
  </main>
</body>
</html>
```